Interval Timer App

Need to have design for the attached wireframe. Similar app can be found here: https://shop.lumaverse.net/store/apps/details?id=cc.quillfern.pulseclock

```html
<!DOCTYPE html>
<html lang="en">
<head>
<meta charset="utf-8">
<title>Interval Timer</title>
<link href="https://fonts.googleapis.com/css2?family=Nunito+Sans:wght@400;600;700&display=swap" rel="stylesheet">
<style>
  :root {
    --bg: #ffffff;
    --ink: #23232f;
    --muted: #555a63;
    --soft: #a9adb3;
    --faint: #d9dbde;
    --blue: #1a80e6;
    --blue-deep: #1570d8;
    --blue-light: #2e93ef;
    --card-shadow: rgba(30, 40, 60, 0.16);
  }
  * { margin: 0; padding: 0; box-sizing: border-box; }
  html, body { width: 675px; height: 1200px; overflow: hidden; background: var(--bg); }
  body { font-family: "Nunito Sans", sans-serif; color: var(--ink); position: relative; }

  .settings-icon { position: absolute; left: 592px; top: 42px; width: 50px; height: 50px; }

  .section-title {
    position: absolute; left: 0; width: 675px; text-align: center;
    font-weight: 600; line-height: 1; transform: translateY(-50%);
  }
  .sets-title { top: 114px; font-size: 38px; }
  .work-title { top: 309px; font-size: 43px; }
  .rest-title { top: 688px; font-size: 43px; }

  .stepper-btn {
    position: absolute; top: 174px; width: 65px; height: 45px; border-radius: 14px;
    background: linear-gradient(180deg, var(--blue-light), var(--blue-deep));
  }
  .stepper-btn::before, .stepper-btn::after {
    content: ""; position: absolute; left: 50%; top: 50%; background: #fff; border-radius: 2px;
    width: 24px; height: 4px; transform: translate(-50%, -50%);
  }
  .stepper-plus::after { width: 4px; height: 24px; }
  .stepper-minus::after { display: none; }
  .stepper-minus { left: 203px; }
  .stepper-plus { left: 409px; }
  .sets-value {
    position: absolute; left: 337px; top: 197px; transform: translate(-50%, -50%);
    font-size: 40px; color: var(--muted); font-weight: 400;
  }

  .picker-card {
    position: absolute; left: 79px; width: 517px; height: 274px; background: #fff;
    border-radius: 8px; overflow: hidden;
    box-shadow: 0 2px 10px var(--card-shadow);
  }
  .work-card { top: 356px; }
  .rest-card { top: 733px; }

  .picker-label {
    position: absolute; left: 0; width: 100%; text-align: center;
    font-size: 24px; color: var(--muted); transform: translateY(-50%);
  }
  .label-minutes { top: 22px; }
  .label-seconds { top: 157px; }

  .picker-row { position: absolute; left: 0; width: 100%; height: 0; }
  .row-minutes { top: 89px; }
  .row-seconds { top: 224px; }

  .num {
    position: absolute; top: 0; transform: translate(-50%, -50%);
    font-size: 29px; color: var(--muted); line-height: 1;
  }
  .num.far { color: var(--soft); }
  .num.edge { color: var(--faint); }
  .num.selected {
    width: 64px; height: 64px; border-radius: 50%; color: #fff;
    display: flex; align-items: center; justify-content: center;
    background: linear-gradient(160deg, var(--blue-light), var(--blue-deep));
  }

  .start-btn {
    position: absolute; left: 217px; top: 1069px; width: 242px; height: 73px;
    border-radius: 37px; background: linear-gradient(180deg, var(--blue-light), var(--blue-deep));
    color: #fff; font-size: 24px; font-weight: 600; letter-spacing: 1.5px;
    display: flex; align-items: center; justify-content: center;
  }
</style>
</head>
<body>
  <svg class="settings-icon" viewBox="0 0 24 24" fill="none" stroke="#1a80e6" stroke-width="1.4" stroke-linecap="round" stroke-linejoin="round" aria-label="Settings">
    <circle cx="12" cy="12" r="3"/>
    <path d="M19.4 15a1.65 1.65 0 0 0 .33 1.82l.06.06a2 2 0 0 1 0 2.83 2 2 0 0 1-2.83 0l-.06-.06a1.65 1.65 0 0 0-1.82-.33 1.65 1.65 0 0 0-1 1.51V21a2 2 0 0 1-2 2 2 2 0 0 1-2-2v-.09A1.65 1.65 0 0 0 9 19.4a1.65 1.65 0 0 0-1.82.33l-.06.06a2 2 0 0 1-2.83 0 2 2 0 0 1 0-2.83l.06-.06a1.65 1.65 0 0 0 .33-1.82 1.65 1.65 0 0 0-1.51-1H3a2 2 0 0 1-2-2 2 2 0 0 1 2-2h.09A1.65 1.65 0 0 0 4.6 9a1.65 1.65 0 0 0-.33-1.82l-.06-.06a2 2 0 0 1 0-2.83 2 2 0 0 1 2.83 0l.06.06a1.65 1.65 0 0 0 1.82.33H9a1.65 1.65 0 0 0 1-1.51V3a2 2 0 0 1 2-2 2 2 0 0 1 2 2v.09a1.65 1.65 0 0 0 1 1.51 1.65 1.65 0 0 0 1.82-.33l.06-.06a2 2 0 0 1 2.83 0 2 2 0 0 1 0 2.83l-.06.06a1.65 1.65 0 0 0-.33 1.82V9a1.65 1.65 0 0 0 1.51 1H21a2 2 0 0 1 2 2 2 2 0 0 1-2 2h-.09a1.65 1.65 0 0 0-1.51 1z"/>
  </svg>

  <h1 class="section-title sets-title">Sets</h1>
  <div class="stepper-btn stepper-minus" aria-label="Decrease sets"></div>
  <div class="sets-value">3</div>
  <div class="stepper-btn stepper-plus" aria-label="Increase sets"></div>

  <h2 class="section-title work-title">Work Interval</h2>
  <section class="picker-card work-card">
    <div class="picker-label label-minutes">Minutes</div>
    <div class="picker-row row-minutes">
      <span class="num edge" style="left:24px">58</span>
      <span class="num" style="left:94px">59</span>
      <span class="num" style="left:144px">1</span>
      <span class="num" style="left:187px">2</span>
      <span class="num selected" style="left:258px">3</span>
      <span class="num" style="left:330px">4</span>
      <span class="num far" style="left:377px">5</span>
      <span class="num far" style="left:424px">6</span>
      <span class="num edge" style="left:469px">7</span>
    </div>
    <div class="picker-label label-seconds">Seconds</div>
    <div class="picker-row row-seconds">
      <span class="num edge" style="left:9px">11</span>
      <span class="num far" style="left:71px">12</span>
      <span class="num" style="left:127px">13</span>
      <span class="num" style="left:187px">14</span>
      <span class="num selected" style="left:258px">15</span>
      <span class="num" style="left:330px">16</span>
      <span class="num" style="left:392px">17</span>
      <span class="num far" style="left:452px">18</span>
      <span class="num edge" style="left:514px">19</span>
    </div>
  </section>

  <h2 class="section-title rest-title">Rest Interval</h2>
  <section class="picker-card rest-card">
    <div class="picker-label label-minutes">Minutes</div>
    <div class="picker-row row-minutes">
      <span class="num far" style="left:52px">57</span>
      <span class="num" style="left:110px">58</span>
      <span class="num" style="left:182px">59</span>
      <span class="num selected" style="left:258px">1</span>
      <span class="num" style="left:330px">2</span>
      <span class="num" style="left:377px">3</span>
      <span class="num far" style="left:424px">4</span>
      <span class="num edge" style="left:470px">5</span>
    </div>
    <div class="picker-label label-seconds">Seconds</div>
    <div class="picker-row row-seconds">
      <span class="num edge" style="left:9px">11</span>
      <span class="num far" style="left:71px">12</span>
      <span class="num" style="left:127px">13</span>
      <span class="num" style="left:187px">14</span>
      <span class="num selected" style="left:258px">15</span>
      <span class="num" style="left:330px">16</span>
      <span class="num" style="left:392px">17</span>
      <span class="num far" style="left:452px">18</span>
      <span class="num edge" style="left:514px">19</span>
    </div>
  </section>

  <div class="start-btn">START</div>
</body>
</html>
```